BOLD & MINIMALIST DESIGN NEEDED

We want a very bold but minimalistic business card design that is impactful and utilizes both sides of the business card. Our current logo is included for your use.

We want bold fonts and good use of negative space. We don't want the logo to overpower the design.

Target Market(s)

Professionals who are building new commercial buildings.

Industry/Entity Type

Construction

Contact Information for Business Card

Name, Title, email, office phone, cell phone, website

Font styles to use
Serif
Sans Serif

Requirements
Must have
• Bold design!

```html
<!DOCTYPE html>
<html lang="en">
<head>
<meta charset="utf-8">
<title>Ridgeline Design + Build — Business Card</title>
<link href="https://fonts.googleapis.com/css2?family=Montserrat:wght@400;500;700;800&display=swap" rel="stylesheet">
<style>
  :root {
    --stage: #3a3a3a;
    --ink: #111111;
    --paper: #ffffff;
    --green: #8cc63f;
    --muted: #222222;
  }
  * { box-sizing: border-box; margin: 0; padding: 0; }
  html, body { width: 1200px; height: 694px; overflow: hidden; }
  body {
    background: var(--stage);
    font-family: 'Montserrat', sans-serif;
    display: flex;
    align-items: center;
    justify-content: center;
    gap: 50px;
  }
  .card {
    position: relative;
    width: 525px;
    height: 300px;
    border-radius: 18px;
    overflow: hidden;
  }
  /* Front */
  .card--front {
    background: var(--ink);
    display: flex;
    align-items: center;
    justify-content: center;
  }
  .brand {
    display: flex;
    align-items: center;
    gap: 14px;
  }
  .brand__mark {
    width: 22px;
    height: 22px;
    background: var(--green);
  }
  .brand__name {
    font-weight: 800;
    line-height: 1.05;
    text-transform: uppercase;
    letter-spacing: 1px;
  }
  .card--front .brand__name { color: var(--paper); font-size: 40px; }
  .brand__name small {
    display: block;
    font-size: 0.42em;
    letter-spacing: 6px;
    margin-top: 6px;
  }
  /* Back */
  .card--back { background: var(--paper); }
  .card--back .brand {
    position: absolute;
    left: 34px;
    top: 96px;
    gap: 10px;
    z-index: 1;
  }
  .card--back .brand__mark { width: 16px; height: 16px; }
  .card--back .brand__name { color: var(--ink); font-size: 27px; }
  .divider {
    position: absolute;
    left: 272px;
    top: 44px;
    width: 2px;
    height: 140px;
    background: var(--ink);
  }
  .contact {
    position: absolute;
    left: 292px;
    top: 36px;
    color: var(--muted);
    z-index: 1;
  }
  .contact__name { font-size: 22px; font-weight: 800; color: var(--ink); line-height: 27px; }
  .contact__title { font-size: 13px; font-weight: 500; line-height: 17px; margin-bottom: 10px; }
  .contact__list { list-style: none; }
  .contact__item {
    display: flex;
    align-items: center;
    gap: 8px;
    font-size: 13px;
    font-weight: 500;
    line-height: 21px;
  }
  .contact__icon { width: 13px; height: 13px; flex: none; }
  .wave {
    position: absolute;
    left: 0;
    top: 0;
    width: 525px;
    height: 300px;
  }
</style>
</head>
<body>
  <section class="card card--front" aria-label="Card front">
    <div class="brand">
      <span class="brand__mark"></span>
      <p class="brand__name">Ridgeline<small>Design + Build</small></p>
    </div>
  </section>

  <section class="card card--back" aria-label="Card back">
    <svg class="wave" viewBox="0 0 525 300" aria-hidden="true">
      <path d="M0,284 C180,282 300,256 380,236 C440,222 490,214 525,210 L525,300 L0,300 Z" fill="var(--ink)"/>
      <path d="M0,272 C180,270 300,242 380,222 C440,208 490,200 525,196" fill="none" stroke="var(--green)" stroke-width="4"/>
    </svg>

    <div class="brand">
      <span class="brand__mark"></span>
      <p class="brand__name">Ridgeline<small>Design + Build</small></p>
    </div>

    <div class="divider"></div>

    <div class="contact">
      <p class="contact__name">Marcus Hale</p>
      <p class="contact__title">Founder &amp; CEO</p>
      <ul class="contact__list">
        <li class="contact__item">
          <svg class="contact__icon" viewBox="0 0 16 16"><path d="M3 1h3l1.5 4-2 1.2a9 9 0 0 0 4.3 4.3L11 8.5l4 1.5v3a2 2 0 0 1-2 2C6.4 15 1 9.6 1 3a2 2 0 0 1 2-2z" fill="var(--green)"/></svg>
          555-210-4400
        </li>
        <li class="contact__item">
          <svg class="contact__icon" viewBox="0 0 16 16"><rect x="4" y="1" width="8" height="14" rx="1.5" fill="none" stroke="var(--green)" stroke-width="1.6"/><circle cx="8" cy="12.5" r="0.9" fill="var(--green)"/></svg>
          555-210-4401
        </li>
        <li class="contact__item">
          <svg class="contact__icon" viewBox="0 0 16 16"><rect x="1" y="3" width="14" height="10" fill="var(--green)"/><path d="M1 3l7 6 7-6" fill="none" stroke="var(--paper)" stroke-width="1.3"/></svg>
          info@ridgeline-db.com
        </li>
        <li class="contact__item">
          <svg class="contact__icon" viewBox="0 0 16 16"><circle cx="8" cy="8" r="7" fill="var(--green)"/><path d="M1 8h14M8 1c-3 3-3 11 0 14M8 1c3 3 3 11 0 14" fill="none" stroke="var(--paper)" stroke-width="1"/></svg>
          www.ridgeline-db.com
        </li>
      </ul>
    </div>
  </section>
</body>
</html>
```